Business Card Design

We are a manufacturing and distribution company with most of our customer base being supermarkets. We have established brand guidelines that are attached.

```html
<!DOCTYPE html>
<html lang="en">
<head>
<meta charset="utf-8">
<title>Corvale Business Card</title>
<link href="https://fonts.googleapis.com/css2?family=Archivo:wdth,wght@62..125,400;62..125,500;62..125,700;62..125,800&display=swap" rel="stylesheet">
<style>
  :root {
    --backdrop: #b8b8b8;
    --card-white: #ffffff;
    --card-black: #221f20;
    --brand-red: #e31b23;
    --brand-blue: #0069aa;
    --shadow: rgba(0, 0, 0, 0.55);
  }
  * { margin: 0; padding: 0; box-sizing: border-box; }
  html, body {
    width: 1075px;
    height: 1200px;
    overflow: hidden;
    background: var(--backdrop);
    font-family: "Archivo", Arial, sans-serif;
  }
  .card {
    position: absolute;
    left: 206px;
    width: 663px;
    height: 395px;
    box-shadow: 3px 3px 0 var(--shadow);
    overflow: hidden;
  }
  .card-front { top: 187px; background: var(--card-white); }
  .card-back { top: 637px; background: var(--card-black); }

  .side-panel {
    position: absolute;
    right: 0;
    top: 0;
    width: 155px;
    height: 100%;
  }
  .side-panel .band-red {
    position: absolute; left: 0; top: 0; width: 100%; height: 200px;
    background: var(--brand-red);
  }
  .side-panel .band-blue {
    position: absolute; left: 0; top: 200px; width: 100%; height: 195px;
    background: var(--brand-blue);
  }
  .panel-name {
    position: absolute;
    left: 0; top: 187px; width: 100%;
    text-align: center;
    color: var(--card-white);
    font-weight: 700;
    font-stretch: 125%;
    font-size: 20px;
    letter-spacing: 1px;
    line-height: 26px;
  }

  .holder { position: absolute; left: 35px; top: 91px; }
  .holder-name {
    color: var(--brand-red);
    font-weight: 700;
    font-size: 23px;
    line-height: 26px;
    letter-spacing: 0.2px;
  }
  .holder-title {
    color: var(--brand-blue);
    font-weight: 400;
    font-size: 17px;
    line-height: 20px;
    letter-spacing: 0.3px;
  }
  .contact-list { position: absolute; left: 35px; top: 159px; list-style: none; }
  .contact-list li {
    display: flex; align-items: center;
    height: 23.5px;
    color: var(--brand-blue);
    font-size: 18px;
  }
  .contact-list svg { width: 17px; height: 17px; margin-right: 6px; flex: none; }
  .address {
    position: absolute; left: 38px; top: 256px;
    color: var(--brand-blue);
    font-size: 18px;
    line-height: 23.5px;
  }

  .back-name {
    position: absolute;
    left: 0; top: 222px; width: 100%;
    text-align: center;
    color: var(--card-white);
    font-weight: 800;
    font-stretch: 125%;
    font-size: 54px;
    line-height: 64px;
    letter-spacing: 1px;
  }
</style>
</head>
<body>
  <section class="card card-front" aria-label="Card front">
    <div class="side-panel">
      <div class="band-red"></div>
      <div class="band-blue"></div>
      <div class="panel-name">CORVALE</div>
    </div>

    <div class="holder">
      <p class="holder-name">DANIEL HARTLEY</p>
      <p class="holder-title">MANAGING DIRECTOR</p>
    </div>

    <ul class="contact-list">
      <li>
        <svg viewBox="0 0 24 24" aria-hidden="true"><path fill="#e31b23" d="M6.6 10.8a15.1 15.1 0 0 0 6.6 6.6l2.2-2.2a1 1 0 0 1 1-.25 11.4 11.4 0 0 0 3.6.57 1 1 0 0 1 1 1V20a1 1 0 0 1-1 1A17 17 0 0 1 3 4a1 1 0 0 1 1-1h3.5a1 1 0 0 1 1 1c0 1.25.2 2.45.57 3.57a1 1 0 0 1-.25 1z"/></svg>
        033-987 210 654
      </li>
      <li>
        <svg viewBox="0 0 24 24" aria-hidden="true"><rect x="2" y="5" width="20" height="14" fill="#e31b23"/><path d="M2 5l10 8 10-8M2 19l7-6M22 19l-7-6" stroke="#fff" stroke-width="1.6" fill="none"/></svg>
        hello@corvale.com
      </li>
      <li>
        <svg viewBox="0 0 24 24" aria-hidden="true"><g fill="none" stroke="#e31b23" stroke-width="2"><circle cx="12" cy="12" r="9"/><ellipse cx="12" cy="12" rx="4" ry="9"/><path d="M3 12h18M5 7h14M5 17h14"/></g></svg>
        www.corvalefoods.com
      </li>
    </ul>

    <p class="address">58, Millbrook Road Unit 4<br>20817, Eastvale</p>
  </section>

  <section class="card card-back" aria-label="Card back">
    <p class="back-name">CORVALE</p>
  </section>
</body>
</html>
```